Local Roofing/Construction company business needs new biz card design

We need a new business card design, current cards are from the start of this operation and generic at best. We are a local Construction Company (General Contractor) with a majority of our work originating from insurance claims-exterior finish work is the main focus (Roofs-Siding-Gutters etc). Heavily involved with homeowners and the low ball offers they receive from insurance company's after a insurable event takes place. I have attached some of our original logo file(s) below.

```html
<!DOCTYPE html>
<html lang="en">
<head>
<meta charset="utf-8">
<title>Ridgeline Builders – Business Card</title>
<link href="https://fonts.googleapis.com/css2?family=Montserrat:wght@500;700;800&display=swap" rel="stylesheet">
<style>
  :root {
    --page-bg: #d6d6d6;
    --card-white: #f4f4f4;
    --brand-green: #4cb96b;
    --green-light: #8fd8a4;
    --green-mid: #62c47e;
    --ink: #1f2a2c;
    --ink-soft: #2b2b2b;
  }
  * { box-sizing: border-box; margin: 0; padding: 0; }
  html, body { width: 1200px; height: 1200px; overflow: hidden; }
  body {
    background: var(--page-bg);
    font-family: "Montserrat", sans-serif;
    color: var(--ink-soft);
    display: flex;
    flex-direction: column;
    align-items: center;
    justify-content: center;
    gap: 60px;
  }
  .card {
    width: 700px;
    height: 400px;
    border-radius: 22px;
    position: relative;
    overflow: hidden;
    box-shadow: 0 6px 18px rgba(0,0,0,0.12);
  }
  .card-back {
    background: linear-gradient(120deg, var(--green-light) 0%, var(--green-mid) 100%);
  }
  .card-back .pattern-area { position: absolute; inset: 0; }
  .card-front { background: var(--card-white); }

  .brand-mark {
    position: absolute;
    top: 62px;
    left: 0; right: 0;
    display: flex;
    align-items: center;
    justify-content: center;
    gap: 16px;
  }
  .brand-mark .brand-square {
    width: 52px; height: 52px;
    background: var(--ink);
    border-radius: 6px;
  }
  .brand-mark .brand-name {
    font-weight: 800;
    font-size: 44px;
    letter-spacing: 1px;
    text-transform: uppercase;
    color: var(--ink);
  }

  .rule { position: absolute; height: 2px; background: var(--brand-green); }
  .rule-top { left: 320px; right: 50px; top: 172px; }
  .rule-mid { left: 50px; right: 50px; top: 268px; }

  .person { position: absolute; left: 290px; top: 188px; }
  .person .name { font-weight: 700; font-size: 28px; color: var(--brand-green); }
  .person .role { font-weight: 500; font-size: 17px; color: var(--ink-soft); margin-top: 4px; margin-left: 30px; }

  .address {
    position: absolute; right: 50px; top: 190px;
    text-align: right; font-weight: 500; font-size: 17px; line-height: 1.35;
  }

  .contacts { position: absolute; left: 50px; top: 288px; list-style: none; }
  .contacts li {
    display: flex; align-items: center; gap: 12px;
    font-weight: 500; font-size: 18px; line-height: 1; margin-bottom: 14px;
  }
  .contacts svg { width: 18px; height: 18px; flex: none; }
</style>
</head>
<body>

  <section class="card card-back">
    <div class="pattern-area" role="img" aria-label="Repeating tiled brand pattern in tonal greens"></div>
  </section>

  <section class="card card-front">
    <div class="brand-mark">
      <span class="brand-square"></span>
      <span class="brand-name">Ridgeline Builders</span>
    </div>

    <div class="rule rule-top"></div>

    <div class="person">
      <p class="name">Marcus Dale</p>
      <p class="role">Founder &amp; Director</p>
    </div>

    <address class="address" style="font-style:normal">
      4820 Alder Lane<br>
      Brookfield Maine<br>
      04011
    </address>

    <div class="rule rule-mid"></div>

    <ul class="contacts">
      <li>
        <svg viewBox="0 0 24 24" aria-hidden="true"><path fill="var(--brand-green)" d="M6.6 10.8a15.1 15.1 0 0 0 6.6 6.6l2.2-2.2a1 1 0 0 1 1-.25 11.4 11.4 0 0 0 3.6.57 1 1 0 0 1 1 1V20a1 1 0 0 1-1 1A17 17 0 0 1 3 4a1 1 0 0 1 1-1h3.5a1 1 0 0 1 1 1c0 1.25.2 2.45.57 3.57a1 1 0 0 1-.25 1z"/></svg>
        (405)-555-0147
      </li>
      <li>
        <svg viewBox="0 0 24 24" aria-hidden="true"><rect x="2" y="5" width="20" height="14" rx="2" fill="var(--brand-green)"/><path d="M3 6.5l9 6 9-6" stroke="#fff" stroke-width="1.6" fill="none"/></svg>
        info@ridgelinebuilders.com
      </li>
      <li>
        <svg viewBox="0 0 24 24" aria-hidden="true"><circle cx="12" cy="12" r="10" fill="var(--brand-green)"/><path d="M2 12h20M12 2c3 3 3 17 0 20M12 2c-3 3-3 17 0 20" stroke="#fff" stroke-width="1.4" fill="none"/></svg>
        www.ridgelinebuilders.com
      </li>
    </ul>
  </section>

</body>
</html>
```